Graphic background for 10 Pull Up Banners

To produce a graphic background for a 100 cm wide by 200 cm high Pull-Up Display banner containing a Buddhist text in three languages: Tibetan, Mandarin and English. Please refer to uploaded file "Elements of Pull Up Banner". The design should be simple (not drawing attention away from the text). This design should then be varied for or extended to the next banner and so on until the 10th banner. When the banners are lined up, they should form a single design that is 1000 cm wide by 200 cm high.
An alternative way to look at the project is to produce a graphic background of 1000 cm width by 200 cm height that is then splitted into ten separate 100 cm wide by 200 cm high graphic to be used as background for 10 Buddhist texts (text 1, 2, 3, 4, 5, 6, 7, 8, 9a, 9b) on 10 Pull-Up Display Banners, the text in each banner being in the three languages mentioned earlier.
In either perspective, the design should be simple and not draw attention away from the texts. See uploaded PDF file "Examples.pdf"
Target Market(s)
For attendees at a Buddhist Event.
Look and feel
Each slider illustrates characteristics of the customer's brand and the style your logo design should communicate.

```html
<!DOCTYPE html>
<html lang="en">
<head>
<meta charset="utf-8">
<title>Dharma Pull-Up Banner Series</title>
<link rel="stylesheet" href="https://fonts.googleapis.com/css2?family=Tinos:wght@400;700&family=Arimo:wght@400&family=Noto+Serif+SC:wght@400;600&family=Noto+Serif+Tibetan&display=swap">
<style>
  :root {
    --lime-top: #d6f53a;
    --lime-mid: #a6e83c;
    --green-deep: #86d940;
    --aqua-soft: #b9f2a0;
    --title-red: #b3142a;
    --body-red: #c2332c;
    --veil: rgba(255, 255, 255, 0.30);
    --veil-soft: rgba(255, 255, 255, 0.22);
    --frame-white: rgba(255, 255, 255, 0.95);
    --emblem-red: #c0392b;
  }
  * { margin: 0; padding: 0; box-sizing: border-box; }
  html, body { width: 1200px; height: 471px; overflow: hidden; background: #ffffff; }
  .banner-row {
    position: relative;
    width: 1200px; height: 471px;
    display: flex;
    background:
      linear-gradient(180deg, rgba(255,255,255,0) 72%, rgba(184,154,74,0.35) 88%, rgba(140,110,50,0.55) 100%),
      linear-gradient(90deg, var(--lime-top) 0%, var(--green-deep) 30%, var(--lime-mid) 55%, var(--green-deep) 78%, var(--aqua-soft) 100%);
  }
  .banner { position: relative; width: 240px; height: 471px; flex: none; }
  .banner-frame { position: absolute; inset: 0; width: 240px; height: 471px; }
  .emblem {
    position: absolute; left: 14px; top: 6px;
    width: 58px; height: 60px;
    border-radius: 6px 6px 14px 14px;
    background: radial-gradient(circle at 50% 40%, #e0685a 0%, var(--emblem-red) 55%, rgba(192,57,43,0.4) 100%);
    opacity: 0.85;
  }
  .title {
    position: absolute; left: 70px; right: 8px; top: 14px;
    font-family: "Tinos", "Times New Roman", serif;
    font-weight: 400;
    color: var(--title-red);
    line-height: 1;
    text-align: center;
  }
  .title .big { font-size: 24px; display: block; }
  .title .small { font-size: 13px; display: block; }
  .title .amp { font-size: 14px; }
  .text-box {
    position: absolute; left: 46px; width: 150px;
    background: var(--veil);
    display: flex; flex-direction: column; justify-content: center; align-items: center;
    text-align: center;
    padding: 3px 2px;
    overflow: hidden;
  }
  .box-tibetan { top: 80px; height: 88px; }
  .box-chinese { top: 180px; height: 82px; }
  .box-english { top: 278px; height: 86px; }
  .tibetan-lines {
    font-family: "Noto Serif Tibetan", serif;
    font-size: 3.6px; line-height: 7px;
    color: var(--body-red);
  }
  .chinese-lines {
    font-family: "Noto Serif SC", serif;
    font-size: 6px; line-height: 7.6px;
    color: var(--body-red);
  }
  .chinese-lines.roomy { font-size: 6.4px; line-height: 9px; }
  .chinese-lines.large { font-size: 9.5px; line-height: 13px; }
  .chinese-lines .note { font-size: 4px; line-height: 7px; display: block; }
  .english-lines {
    font-family: "Arimo", Arial, sans-serif;
    font-size: 3.8px; line-height: 7px;
    color: var(--body-red);
  }
  .english-lines p + p { margin-top: 4px; }
  .english-lines.large { font-size: 4.1px; line-height: 11px; }
  .dedication {
    position: absolute; left: 54px; top: 396px;
    width: 134px; height: 50px;
    background: var(--veil-soft);
    text-align: center;
    padding-top: 5px;
    color: var(--title-red);
  }
  .dedication .tib { font-family: "Noto Serif Tibetan", serif; font-size: 4px; line-height: 9px; }
  .dedication .zh { font-family: "Noto Serif SC", serif; font-size: 6.5px; line-height: 11px; }
  .dedication .en { font-family: "Tinos", "Times New Roman", serif; font-size: 6px; line-height: 11px; }
</style>
</head>
<body>
<main class="banner-row">

  <!-- Banner 1 -->
  <section class="banner">
    <svg class="banner-frame" viewBox="0 0 240 471" aria-hidden="true">
      <path d="M8 30 Q8 10 28 8 M212 8 Q232 10 232 30 M8 30 V440 Q8 462 28 462 M232 30 V440 Q232 462 212 462" fill="none" stroke="var(--frame-white)" stroke-width="1"/>
    </svg>
    <div class="emblem" role="img" aria-label="Red deity emblem on a lotus throne"></div>
    <h2 class="title"><span class="big">Ten Mistaking</span></h2>
    <div class="text-box box-tibetan">
      <p class="tibetan-lines">
        དད་པ་དང་ཆགས་པ་ནོར་སྲིད། བརྩེ་བ་དང་ཞེན་པ་ནོར་སྲིད།<br>
        སྙིང་རྗེ་དང་སྡུག་བསྔལ་ནོར་སྲིད། ཤེས་རབ་དང་རྟོག་པ་ནོར་སྲིད།<br>
        སྟོང་ཉིད་དང་ཆད་ལྟ་ནོར་སྲིད། སྒོམ་དང་ཡིད་འཕྲོ་ནོར་སྲིད།<br>
        བཟོད་པ་དང་ལེ་ལོ་ནོར་སྲིད། བརྩོན་འགྲུས་དང་འདོད་པ་ནོར་སྲིད།<br>
        ཆོས་དང་ཆོས་ལྟར་བཅོས་པ་ནོར་སྲིད། བླ་མ་དང་ལོག་འདྲེན་ནོར་སྲིད།<br>
        དེ་དག་ལེགས་པར་ཤེས་པར་གྱིས། སེམས་ཀྱི་རང་བཞིན་རྟོགས་པར་ཤོག<br>
        སྐྱེ་བོ་ཀུན་གྱིས་ལམ་བཟང་འགྲུབ། བདེ་ལེགས་ཕུན་སུམ་ཚོགས་པར་ཤོག
      </p>
    </div>
    <div class="text-box box-chinese">
      <p class="chinese-lines">
        信心与贪恋可能混淆，<br>
        悲心与多愁可能混淆，<br>
        空性与断见可能混淆，<br>
        禅修与散乱可能混淆，<br>
        安忍与懈怠可能混淆，<br>
        精进与贪求可能混淆，<br>
        佛法与伪法可能混淆，<br>
        上师与邪师可能混淆。
        <span class="note">— 出自：十种混淆之说 —</span>
      </p>
    </div>
    <div class="text-box box-english">
      <div class="english-lines">
        Desire can be mistaken for faith in devotion.<br>
        Attachment can be mistaken for love and compassion.<br>
        Sorrow can be mistaken for the kindness of a caring heart.<br>
        Inertia can be mistaken for the stillness of meditation.<br>
        A wandering mind can be mistaken for clear insight.<br>
        Indifference can be mistaken for the practice of patience.<br>
        Craving can be mistaken for diligence on the path.<br>
        Empty views can be mistaken for wisdom of emptiness.<br>
        Imitation of Dharma can be mistaken for the Dharma itself.<br>
        A false guide can be mistaken for a true teacher.<br>
        Know each one clearly, and do not be misled.
      </div>
    </div>
    <div class="dedication">
      <p class="tib">སེམས་ཅན་ཐམས་ཅད་སངས་རྒྱས་ཐོབ་པར་ཤོག</p>
      <p class="zh">愿诸有情共证佛果位</p>
      <p class="en">May all attain Buddhahood together.</p>
    </div>
  </section>

  <!-- Banner 2 -->
  <section class="banner">
    <svg class="banner-frame" viewBox="0 0 240 471" aria-hidden="true">
      <path d="M8 30 Q8 10 28 8 M212 8 Q232 10 232 30 M8 30 V440 Q8 462 28 462 M232 30 V440 Q232 462 212 462" fill="none" stroke="var(--frame-white)" stroke-width="1"/>
    </svg>
    <div class="emblem" role="img" aria-label="Red deity emblem on a lotus throne"></div>
    <h2 class="title"><span class="big">Desire <span class="amp">&amp;</span></span><span class="big">Attachment</span></h2>
    <div class="text-box box-tibetan">
      <p class="tibetan-lines">
        འདོད་པ་མེད་ན་རང་དོན་མི་འགྲུབ་སྟེ།<br>
        འདོད་པ་ཡོད་ཀྱང་ཞེན་པ་མ་ཡིན་པས།<br>
        འདོད་པ་དང་ཞེན་པའི་ཁྱད་པར་མི་ཤེས་ན།<br>
        ཆགས་པ་ལམ་དུ་ཁྱེར་ཞེས་སྨྲ་བ་ནོར།
      </p>
    </div>
    <div class="text-box box-chinese">
      <p class="chinese-lines large">
        若无意欲则不成自利，<br>
        然有意欲非为执着故，<br>
        不知意欲执着差别即，<br>
        贪执说所当取确荒唐。
      </p>
    </div>
    <div class="text-box box-english">
      <div class="english-lines large">
        If you have no desire, your goal cannot be achieved.<br>
        Since not all desire is attachment,<br>
        not knowing how to differentiate desire from attachment,<br>
        to talk about bringing passion into the path is absurd.
      </div>
    </div>
    <div class="dedication">
      <p class="tib">སེམས་ཅན་ཐམས་ཅད་སངས་རྒྱས་ཐོབ་པར་ཤོག</p>
      <p class="zh">愿诸有情共证佛果位</p>
      <p class="en">May all attain Buddhahood together.</p>
    </div>
  </section>

  <!-- Banner 3 -->
  <section class="banner">
    <svg class="banner-frame" viewBox="0 0 240 471" aria-hidden="true">
      <path d="M8 30 Q8 10 28 8 M212 8 Q232 10 232 30 M8 30 V440 Q8 462 28 462 M232 30 V440 Q232 462 212 462" fill="none" stroke="var(--frame-white)" stroke-width="1"/>
    </svg>
    <div class="emblem" role="img" aria-label="Red deity emblem on a lotus throne"></div>
    <h2 class="title"><span class="small">Signs of Having Practised</span><span class="big">The Dharma</span></h2>
    <div class="text-box box-tibetan">
      <p class="tibetan-lines">
        ལུས་དང་སྲོག་ལ་མ་ཆགས་པར་ཆོས་བྱེད་ན།<br>
        དོན་དམ་པའི་མིག་ཐོབ་པའི་རྟགས་ཡིན་ནོ།<br>
        གསེར་དང་བོང་བ་མཉམ་པར་མཐོང་བ་ན།<br>
        མི་རྟག་སྒྱུ་མའི་བློ་སྐྱེས་པའི་རྟགས་ཡིན།<br>
        དགྲ་དང་གཉེན་ལ་ཕྱོགས་ལྷུང་མེད་པ་ན།<br>
        འཁོར་བའི་རྒྱ་མཚོ་ལས་བརྒལ་བའི་རྟགས་ཡིན།<br>
        རྗེ་བཙུན་གྱི་གསུང་ལས་བྱུང་བ།
      </p>
    </div>
    <div class="text-box box-chinese">
      <p class="chinese-lines roomy">
        若懂舍弃身命而修行，<br>
        表示取得真实眼满义；<br>
        若懂金与土块平等观，<br>
        表示「无常」「如幻」心中生；<br>
        若视敌亲众为亲人，<br>
        表示摆脱苦海之彼岸。
        <span class="note">— 出自：八督和千里法 —</span>
      </p>
    </div>
    <div class="text-box box-english">
      <div class="english-lines">
        <p>If you do not care for life and limb but give yourself to the Dharma, it is a sign that you have gained the eye of true meaning.</p>
        <p>If you see gold and a lump of earth as equal, it is a sign that impermanence and illusion have arisen in your mind.</p>
        <p>If you hold foe and friend with an even heart, it is a sign that you are leaving the ocean of suffering behind.</p>
        <p>— Sayings of the masters on signs of true practice</p>
      </div>
    </div>
    <div class="dedication">
      <p class="tib">སེམས་ཅན་ཐམས་ཅད་སངས་རྒྱས་ཐོབ་པར་ཤོག</p>
      <p class="zh">愿诸有情共证佛果位</p>
      <p class="en">May all attain Buddhahood together.</p>
    </div>
  </section>

  <!-- Banner 4 -->
  <section class="banner">
    <svg class="banner-frame" viewBox="0 0 240 471" aria-hidden="true">
      <path d="M8 30 Q8 10 28 8 M212 8 Q232 10 232 30 M8 30 V440 Q8 462 28 462 M232 30 V440 Q232 462 212 462" fill="none" stroke="var(--frame-white)" stroke-width="1"/>
    </svg>
    <div class="emblem" role="img" aria-label="Red deity emblem on a lotus throne"></div>
    <h2 class="title"><span class="big">Kindness</span><span class="small">of the <span style="font-size:24px">Guru</span></span></h2>
    <div class="text-box box-tibetan">
      <p class="tibetan-lines">
        བླ་མ་མ་བརྗེད་དྲན་པར་གྱིས།<br>
        སངས་རྒྱས་མང་པོ་བྱོན་ཡང་ང་ལ་སུས་ཀྱང་མ་བཟུང་ངོ་།<br>
        ཁྱེད་ཀྱིས་ང་མ་བོར་བར་བརྩེ་བ་དང་ཐུགས་རྗེས་བསྐྱངས།<br>
        ཁྱེད་ཀྱི་བཀའ་དྲིན་སངས་རྒྱས་སྟོང་ལས་ཆེ།
      </p>
    </div>
    <div class="text-box box-chinese">
      <p class="chinese-lines large">
        切莫忘记上师。<br>
        即使众多佛降临，<br>
        指皆未曾摄受我，<br>
        您不舍弃悲悯护，<br>
        您比千佛恩更大。
      </p>
    </div>
    <div class="text-box box-english">
      <div class="english-lines large">
        Do not forget the guru.<br>
        Although many Buddhas had appeared, none has taken hold of me.<br>
        You did not abandon me, but lovingly and compassionately protected me.<br>
        Your kindness is greater than a thousand Buddhas'.
      </div>
    </div>
    <div class="dedication">
      <p class="tib">སེམས་ཅན་ཐམས་ཅད་སངས་རྒྱས་ཐོབ་པར་ཤོག</p>
      <p class="zh">愿诸有情共证佛果位</p>
      <p class="en">May all attain Buddhahood together.</p>
    </div>
  </section>

  <!-- Banner 5 -->
  <section class="banner">
    <svg class="banner-frame" viewBox="0 0 240 471" aria-hidden="true">
      <path d="M8 30 Q8 10 28 8 M212 8 Q232 10 232 30 M8 30 V440 Q8 462 28 462 M232 30 V440 Q232 462 212 462" fill="none" stroke="var(--frame-white)" stroke-width="1"/>
    </svg>
    <div class="emblem" role="img" aria-label="Red deity emblem on a lotus throne"></div>
    <h2 class="title"><span class="small" style="font-size:17px">You and</span><span class="big">The Dharma</span></h2>
    <div class="text-box box-tibetan">
      <p class="tibetan-lines">
        ཆོས་སྒོ་བརྒྱད་ཁྲི་བཞི་སྟོང་གི་རྩ་བ་ནི།<br>
        རང་སེམས་འདུལ་བ་གཅིག་ལ་འདུས་པ་ཡིན།<br>
        རང་རྒྱུད་མ་ཐུལ་ན་ཆོས་མང་ཐོས་ཀྱང་།<br>
        འཆི་བའི་དུས་སུ་ཕན་པ་ཐོགས་པར་དཀའ།<br>
        ཚིག་གི་ཆོས་ཀྱིས་ཕྱི་མར་ཕན་མི་ཐོགས།<br>
        སེམས་དང་ཆོས་ནི་འདྲེས་པར་གྱིས་ཤིག<br>
        དེ་ནི་ཆོས་ཀྱི་རྩེ་མོ་ཡིན་ནོ།
      </p>
    </div>
    <div class="text-box box-chinese">
      <p class="chinese-lines">
        八万四千法门之根本，<br>
        摄于调伏自心一事中。<br>
        未伏自续纵闻千万教，<br>
        仅缘起外殊时难裨益。<br>
        纵时无益则披离法语，<br>
        对于后世界难起利益，<br>
        故对于法无需求名声，<br>
        自心与法相合时刻中，<br>
        于此实修已得把握，<br>
        纵不欢喜亦为法顶峰。
      </p>
    </div>
    <div class="text-box box-english">
      <div class="english-lines">
        The eighty-four thousand Dharma doors<br>
        are solely for subduing your own mind.<br>
        If your mind is not tamed despite countless instructions,<br>
        apart from making karmic connections, it is hard for those<br>
        instructions to help you at the time of death.<br>
        When lofty Dharma language does not help you at death,<br>
        it is harder for it to benefit you in your next life.<br>
        Thus, famous teachings are not needed.<br>
        Instead, your mind and the Dharma should mix internally.<br>
        And when through practice you gained certainty,<br>
        that is the peak of Dharma, even if others are not delighted.
      </div>
    </div>
    <div class="dedication">
      <p class="tib">སེམས་ཅན་ཐམས་ཅད་སངས་རྒྱས་ཐོབ་པར་ཤོག</p>
      <p class="zh">愿诸有情共证佛果位</p>
      <p class="en">May all attain Buddhahood together.</p>
    </div>
  </section>

</main>
</body>
</html>
```